Clean business card with logo provided

I want a card that will stand out among the masses. I need the color and image to show professionalism and yet have a family appeal showing that I only deal with win/win scenarios. The back of the card will be used to take notes about the individual so I can use that in my database entry. I like modern design but need professionalism in it also. It needs to fit my "clean, safe, and affordable housing" motto. I need to be able to write on the file and update the card details for my employees.

Target Market(s)

Investors looking to make investment income through real estate

Industry/Entity Type

Real Estate

Contact Information for Business Card

Brent Kovalich
blank address, city, st, zip code
480-555-3174
brentkovalich@ridgeworthrentals.example
www.ridgeworthrentals.example

Font styles to use
Sans Serif

Requirements
Must have
• I would like the back of the card to have lines for info. example
• Met/Visited: Date:
• Interets:
Nice to have
• I want the cards color to match the logo background color. Font with details to be san serif and black. I want the card rectangular with square corners. Standard business card size. I would like to see cards designed with both images to see which i prefer more.

```html
<!DOCTYPE html>
<html lang="en">
<head>
<meta charset="utf-8">
<title>Ridgeworth Rentals LLC – Business Card</title>
<link rel="stylesheet" href="https://fonts.googleapis.com/css2?family=Lato:wght@400;700&family=Marcellus&display=swap">
<style>
  :root{
    --teal:#22c2d6;
    --teal-deep:#1aa9bc;
    --ink:#0c0c0d;
    --card-black:#0a0a0b;
    --white:#f2f2f2;
    --stage:#d9dcdd;
  }
  *{box-sizing:border-box;margin:0;padding:0}
  html,body{width:1200px;height:900px;overflow:hidden;background:var(--stage)}
  body{position:relative;font-family:"Lato",Arial,sans-serif}

  .card{position:absolute;left:250px;width:700px;height:400px;overflow:hidden}
  .card--back{top:30px;background:linear-gradient(135deg,var(--teal) 0%,var(--teal-deep) 100%);color:var(--ink)}
  .card--front{top:470px;background:var(--card-black);color:var(--white)}

  /* back: note lines */
  .note-row{position:absolute;display:flex;align-items:flex-end;font-size:19px;letter-spacing:.3px}
  .note-row .label{white-space:nowrap;margin-right:8px}
  .note-row .line{flex:1;border-bottom:2px dotted rgba(255,255,255,.75);height:1px;margin-bottom:4px}
  .row-met{left:40px;top:56px;width:330px}
  .row-time{left:390px;top:56px;width:270px}
  .row-date{left:40px;top:110px;width:330px}
  .row-interests{right:40px;top:110px;width:260px;justify-content:flex-end}
  .row-interests .label{text-transform:uppercase;margin-right:0}
  .blank-line{position:absolute;right:40px;width:260px;border-bottom:2px dotted rgba(255,255,255,.75)}
  .blank-1{top:185px}
  .blank-2{top:235px}

  /* wordmark */
  .wordmark{position:absolute;left:40px;display:flex;align-items:center;gap:12px}
  .wordmark .dot{width:12px;height:12px;border-radius:50%;flex:none}
  .wordmark .name{font-family:"Lato",Arial,sans-serif;font-weight:400;font-size:30px;letter-spacing:2px;text-transform:uppercase;line-height:1;white-space:nowrap}
  .tagline{position:absolute;left:64px;font-size:13px;letter-spacing:.4px}
  .card--back .wordmark{top:300px}
  .card--back .wordmark .dot{background:var(--ink)}
  .card--back .wordmark .name{color:var(--ink)}
  .card--back .tagline{top:342px;color:rgba(255,255,255,.85)}

  /* front */
  .holder-name{position:absolute;left:40px;top:40px;font-family:"Marcellus",Georgia,serif;font-size:38px;letter-spacing:1.5px;color:var(--teal);text-transform:uppercase;font-weight:400}
  .contact-list{position:absolute;left:44px;top:100px;list-style:none;font-size:20px;line-height:1.5}
  .contact-list li{display:flex;align-items:center;gap:12px}
  .contact-list svg{width:16px;height:16px;flex:none}
  .divider{position:absolute;left:0;right:40px;top:222px;height:1.5px;background:linear-gradient(90deg,rgba(34,194,214,.15),var(--teal))}
  .card--front .wordmark{top:316px}
  .card--front .wordmark .dot{background:var(--teal)}
  .card--front .wordmark .name{color:var(--teal)}
  .card--front .tagline{top:358px;color:var(--teal)}
  .address{position:absolute;right:40px;top:240px;display:flex;gap:10px;font-size:20px;line-height:1.35}
  .address svg{width:16px;height:20px;margin-top:4px;flex:none}
</style>
</head>
<body>

<section class="card card--back" aria-label="Card back with note lines">
  <div class="note-row row-met"><span class="label">Meet/Visited:</span><span class="line"></span></div>
  <div class="note-row row-time"><span class="label">Time:</span><span class="line"></span></div>
  <div class="note-row row-date"><span class="label">Date:</span><span class="line"></span></div>
  <div class="note-row row-interests"><span class="label">Interets:</span></div>
  <div class="blank-line blank-1"></div>
  <div class="blank-line blank-2"></div>

  <div class="wordmark"><span class="dot"></span><span class="name">Ridgeworth Rentals LLC</span></div>
  <p class="tagline">Providing clean, safe, and affordable housing</p>
</section>

<section class="card card--front" aria-label="Card front with contact details">
  <h1 class="holder-name">Brent Kovalich</h1>
  <ul class="contact-list">
    <li>
      <svg viewBox="0 0 16 16" aria-hidden="true"><path fill="#22c2d6" d="M3.5 1.5l2.5 3-1.4 1.6c.8 1.9 2.4 3.5 4.3 4.3l1.6-1.4 3 2.5-1.5 2.5C7.3 14 2 8.7 1 3z"/></svg>
      <span>480-555-3174</span>
    </li>
    <li>
      <svg viewBox="0 0 16 16" aria-hidden="true"><circle cx="8" cy="8" r="6.5" fill="none" stroke="#22c2d6" stroke-width="1.5"/><path d="M1.5 8h13M8 1.5c-3 3.5-3 9.5 0 13M8 1.5c3 3.5 3 9.5 0 13" fill="none" stroke="#22c2d6" stroke-width="1.2"/></svg>
      <span>www.ridgeworthrentals.example</span>
    </li>
    <li>
      <svg viewBox="0 0 16 16" aria-hidden="true"><rect x="1.5" y="3.5" width="13" height="9" fill="none" stroke="#22c2d6" stroke-width="1.5"/><path d="M1.5 3.5L8 9l6.5-5.5" fill="none" stroke="#22c2d6" stroke-width="1.5"/></svg>
      <span>brentkovalich@ridgeworthrentals.example</span>
    </li>
  </ul>

  <div class="divider"></div>

  <div class="address">
    <svg viewBox="0 0 16 20" aria-hidden="true"><path fill="#22c2d6" d="M8 0a6 6 0 0 0-6 6c0 4.5 6 14 6 14s6-9.5 6-14a6 6 0 0 0-6-6zm0 8.5A2.5 2.5 0 1 1 8 3.5a2.5 2.5 0 0 1 0 5z"/></svg>
    <p>blank address<br>city, st, zip code</p>
  </div>

  <div class="wordmark"><span class="dot"></span><span class="name">Ridgeworth Rentals LLC</span></div>
  <p class="tagline">Providing clean, safe, and affordable housing</p>
</section>

</body>
</html>
```